Global (re)insurance broker needs a business card design

We need a classic business card for our company that is headquartered in SG, with offices in Malaysia and Dubai. We specialise in insurance and reinsurance broking and consultancy for our global clients.

```html
<!DOCTYPE html>
<html lang="en">
<head>
<meta charset="utf-8">
<title>Kalvern Business Card</title>
<link rel="stylesheet" href="https://fonts.googleapis.com/css2?family=Montserrat:wght@700&family=Open+Sans:wght@400;600&display=swap">
<style>
  :root {
    --stage: #2a2a2d;
    --card-black: #161617;
    --brand-blue: #2448a0;
    --mint: #c3dcb8;
    --text-light: #f2f2f2;
  }
  * { margin: 0; padding: 0; box-sizing: border-box; }
  html, body { width: 1200px; height: 947px; overflow: hidden; }
  body {
    background: var(--stage);
    display: flex;
    flex-direction: column;
    align-items: center;
    justify-content: center;
    gap: 56px;
    font-family: "Open Sans", sans-serif;
  }
  .card {
    width: 580px;
    height: 332px;
    border-radius: 22px;
    position: relative;
    overflow: hidden;
  }
  .card-back {
    background: var(--brand-blue);
  }
  .card-back .pattern-fill {
    position: absolute;
    inset: 0;
    background: linear-gradient(135deg, #2a4fab 0%, #2146a0 55%, #1f419a 100%);
  }
  .card-front {
    background: var(--card-black);
    border: 4px solid var(--brand-blue);
  }
  .brand-name {
    position: absolute;
    left: 56px;
    top: 50%;
    transform: translateY(-50%);
    font-family: "Montserrat", sans-serif;
    font-weight: 700;
    font-size: 44px;
    line-height: 1;
    letter-spacing: 1px;
    white-space: nowrap;
    color: var(--mint);
  }
  .divider {
    position: absolute;
    left: 336px;
    top: 58px;
    width: 1.5px;
    height: 216px;
    background: var(--mint);
  }
  .details {
    position: absolute;
    left: 358px;
    top: 56px;
    right: 12px;
    color: var(--text-light);
    font-size: 13.5px;
    line-height: 1.35;
    white-space: nowrap;
  }
  .person-name {
    font-family: "Montserrat", sans-serif;
    font-weight: 700;
    font-size: 21px;
    color: var(--brand-blue);
    line-height: 1.1;
  }
  .person-title { font-size: 14px; margin-bottom: 14px; }
  .contact-list { list-style: none; margin-bottom: 16px; }
  .contact-list li { display: flex; align-items: center; gap: 7px; }
  .contact-list svg { width: 11px; height: 11px; flex: none; }
  .address { font-size: 14px; }
</style>
</head>
<body>
  <section class="card card-back">
    <div class="pattern-fill" role="img" aria-label="Repeating brand name pattern in darker blue across the card back"></div>
  </section>

  <section class="card card-front">
    <div class="brand-name">KALVERN</div>
    <div class="divider"></div>
    <div class="details">
      <p class="person-name">Mira Lowell</p>
      <p class="person-title">Chief Operating Officer</p>
      <ul class="contact-list">
        <li>
          <svg viewBox="0 0 12 12"><path fill="#c3dcb8" d="M2.5 1h2l1 2.6-1.3.9a6 6 0 0 0 3.3 3.3l.9-1.3L11 7.5v2c0 .8-.7 1.5-1.5 1.5A8.5 8.5 0 0 1 1 2.5C1 1.7 1.7 1 2.5 1z"/></svg>
          +65 6123 4580
        </li>
        <li>
          <svg viewBox="0 0 12 12"><rect x="1" y="2.5" width="10" height="7" rx="1" fill="#c3dcb8"/><path d="M1.5 3l4.5 3.5L10.5 3" fill="none" stroke="#161617" stroke-width="1"/></svg>
          mira@kalvern.com
        </li>
        <li>
          <svg viewBox="0 0 12 12"><circle cx="6" cy="6" r="5" fill="#c3dcb8"/><path d="M1 6h10M6 1c-2 2.7-2 7.3 0 10M6 1c2 2.7 2 7.3 0 10" fill="none" stroke="#161617" stroke-width=".8"/></svg>
          www.kalvern.com
        </li>
      </ul>
      <p class="address">28 Harbour Lane,<br>Marina Tower #12-04,<br>Singapore 018956</p>
    </div>
  </section>
</body>
</html>
```